Heron Loan Partners Business Card

We need a business card design for our mortgage servicing company. In addition to servicing the loans of homeowners, we help homeowners with purchasing their homes and any mortgage refinancing. We would like to see designs that use the colors in the logo attached below (gold-ish yellow and navy blue), and any other design you deem fit! The design should communicate a simpler life with smart mortgages provided by Heron.

```html
<!DOCTYPE html>
<html lang="en">
<head>
<meta charset="utf-8">
<title>Heron Loan Partners – Business Card</title>
<link rel="stylesheet" href="https://fonts.googleapis.com/css2?family=Montserrat:wght@400;500;600;700&display=swap">
<style>
  :root {
    --navy: #282256;
    --gold: #e0b141;
    --paper: #ffffff;
    --ink: #1c1c1c;
    --stage: #2b2b2b;
  }
  * { box-sizing: border-box; margin: 0; padding: 0; }
  html, body { width: 1200px; height: 1015px; overflow: hidden; }
  body {
    background: var(--stage);
    font-family: "Montserrat", sans-serif;
    position: relative;
  }
  .card {
    position: absolute;
    left: 280px;
    width: 640px;
    height: 365px;
    overflow: hidden;
  }
  .card--front { top: 100px; background: var(--navy); }
  .card--back { top: 540px; background: var(--paper); }

  /* front */
  .front-band {
    position: absolute; left: 0; right: 0;
    top: 258px; height: 40px;
    background: var(--gold);
  }
  .front-logo {
    position: absolute; left: 0; right: 0; top: 120px;
    display: flex; justify-content: center; align-items: center; gap: 14px;
  }
  .brand-mark {
    width: 22px; height: 22px; border-radius: 50%;
    background: var(--gold);
  }
  .brand-name {
    font-weight: 700; font-size: 40px; color: var(--gold);
    letter-spacing: 0.5px;
  }
  .front-web {
    position: absolute; left: 0; right: 0; top: 228px;
    text-align: center; font-size: 15px; font-weight: 500;
    color: var(--gold); letter-spacing: 0.5px;
  }

  /* back */
  .back-logo {
    position: absolute; left: 36px; top: 166px;
    display: flex; align-items: center; gap: 10px;
  }
  .back-logo .brand-mark { width: 14px; height: 14px; background: var(--navy); }
  .back-logo .brand-name { font-size: 22px; color: var(--navy); }
  .divider {
    position: absolute; left: 310px; top: 70px;
    width: 1px; height: 185px; background: var(--navy);
  }
  .contact { position: absolute; left: 334px; top: 70px; }
  .person-name {
    font-weight: 700; font-size: 21px; color: var(--gold);
    letter-spacing: 0.5px;
  }
  .person-role {
    font-weight: 500; font-size: 13px; color: var(--navy);
    letter-spacing: 0.4px; margin-bottom: 14px;
  }
  .contact-list { list-style: none; font-size: 14px; color: var(--ink); }
  .contact-list li { display: flex; align-items: center; gap: 9px; line-height: 22px; }
  .contact-list svg { width: 14px; height: 14px; flex: none; }
  .address { margin-top: 10px; margin-left: 23px; font-size: 14px; line-height: 20px; color: var(--ink); }
  .back-bar-gold {
    position: absolute; left: 0; bottom: 0;
    width: 392px; height: 22px; background: var(--gold);
  }
  .back-bar-navy {
    position: absolute; left: 400px; right: 0; bottom: 0;
    height: 22px; background: var(--navy);
  }
</style>
</head>
<body>
  <section class="card card--front">
    <div class="front-logo">
      <span class="brand-mark"></span>
      <span class="brand-name">Heron Loan Partners</span>
    </div>
    <p class="front-web">www.heronloanpartners.com</p>
    <div class="front-band"></div>
  </section>

  <section class="card card--back">
    <div class="back-logo">
      <span class="brand-mark"></span>
      <span class="brand-name">Heron Loan Partners</span>
    </div>
    <div class="divider"></div>
    <div class="contact">
      <h1 class="person-name">DANIEL REYES</h1>
      <p class="person-role">MANAGING DIRECTOR</p>
      <ul class="contact-list">
        <li>
          <svg viewBox="0 0 24 24" aria-hidden="true"><path fill="#e0b141" d="M6.6 10.8a15 15 0 0 0 6.6 6.6l2.2-2.2a1 1 0 0 1 1-.25 11.4 11.4 0 0 0 3.6.57 1 1 0 0 1 1 1V20a1 1 0 0 1-1 1A17 17 0 0 1 3 4a1 1 0 0 1 1-1h3.5a1 1 0 0 1 1 1c0 1.25.2 2.45.57 3.57a1 1 0 0 1-.25 1z"/></svg>
          044-555 018 224
        </li>
        <li>
          <svg viewBox="0 0 24 24" aria-hidden="true"><rect x="2" y="5" width="20" height="14" fill="#e0b141"/><path d="M2 5l10 8 10-8" fill="none" stroke="#fff" stroke-width="2"/></svg>
          info@heronloan.com
        </li>
        <li>
          <svg viewBox="0 0 24 24" aria-hidden="true"><circle cx="12" cy="12" r="10" fill="#e0b141"/><path d="M2 12h20M12 2c3 3 3 17 0 20M12 2c-3 3-3 17 0 20" fill="none" stroke="#fff" stroke-width="1.4"/></svg>
          www.heronloanpartners.com
        </li>
      </ul>
      <p class="address">88, Harbor Street, Suite 4<br>30211, Bayview</p>
    </div>
    <div class="back-bar-gold"></div>
    <div class="back-bar-navy"></div>
  </section>
</body>
</html>
```